Web Developer Needs a Business Card Design

I need a personal business card design that represents me as a web developer for potential employers. I would like the background to be a dark color on the front for contrast with my logo and name. The back will have all my information along with a smaller version of the logo. I want something with a modern look and feel, not too conservative. This will be used for potential employers and freelance work.

Industry/Entity Type

Business

Contact Information for Business Card

Front should have my logo and name. The back should have all my personal information which would include: name: Tom Varulek, phone: 570-614-3098, email: tomvarulek@quillbox.net, website url: www.tomvarulek.net, logo, web developer.

Font styles to use
Sans Serif

Requirements
Must have
• Must include my logo. The color palette base color will be the logo color.

```html
<!DOCTYPE html>
<html lang="en">
<head>
<meta charset="UTF-8">
<title>Tom Varulek — Business Card</title>
<link rel="stylesheet" href="https://fonts.googleapis.com/css2?family=Open+Sans:ital,wght@0,400;0,600;1,700&display=swap">
<style>
  :root {
    --stage: #141414;
    --card: #0b0b0b;
    --card-sheen: #1c1c1c;
    --accent: #72c6b2;
    --ink: #e8e8e8;
    --ink-soft: #cfcfcf;
  }
  * { box-sizing: border-box; margin: 0; padding: 0; }
  html, body {
    width: 1200px; height: 864px; overflow: hidden;
    background: var(--stage);
    font-family: "Open Sans", Arial, sans-serif;
  }
  .stage {
    width: 1200px; height: 864px;
    display: flex; align-items: center; justify-content: center; gap: 40px;
  }
  .card {
    position: relative;
    width: 540px; height: 309px;
    background: linear-gradient(135deg, var(--card-sheen) 0%, var(--card) 55%, #050505 100%);
    box-shadow: 0 18px 40px rgba(0,0,0,.6);
    overflow: hidden;
  }
  /* accent tabs on the info side */
  .accent-tab {
    position: absolute; top: 14%; height: 72%; width: 14px;
    background: var(--accent);
  }
  .accent-tab--left { left: 0; border-radius: 0 9px 9px 0; }
  .accent-tab--right { right: 0; border-radius: 9px 0 0 9px; }
  .divider {
    position: absolute; left: 50%; top: 12%; height: 76%; width: 1px;
    background: var(--accent); opacity: .8;
  }
  .contact {
    position: absolute; left: 40px; top: 82px; width: 220px;
  }
  .contact__name {
    color: var(--accent); font-weight: 700; font-style: italic; font-size: 17px;
  }
  .contact__role {
    color: var(--ink-soft); font-size: 12.5px; margin-bottom: 14px;
  }
  .contact__list { list-style: none; }
  .contact__item {
    display: flex; align-items: center; gap: 9px;
    color: var(--ink); font-size: 13px; line-height: 21px;
  }
  .contact__icon {
    width: 14px; height: 14px; border-radius: 3px; background: var(--accent);
    display: inline-flex; align-items: center; justify-content: center; flex: none;
  }
  .brand {
    position: absolute; display: flex; flex-direction: column; align-items: center; gap: 14px;
  }
  .brand--info { left: 50%; width: 50%; top: 86px; }
  .brand--front { left: 0; width: 100%; top: 92px; }
  .brand__dot {
    width: 66px; height: 66px; border-radius: 50%; background: var(--accent);
  }
  .brand__name {
    color: var(--ink); font-size: 23px; font-weight: 400; letter-spacing: .5px;
  }
</style>
</head>
<body>
<main class="stage">
  <section class="card card--info" aria-label="Card back with contact details">
    <div class="accent-tab accent-tab--left"></div>
    <div class="contact">
      <p class="contact__name">Tom Varulek</p>
      <p class="contact__role">Web Developer</p>
      <ul class="contact__list">
        <li class="contact__item">
          <span class="contact__icon"><svg width="9" height="9" viewBox="0 0 10 10"><path d="M2 1l2 2-1 1.3a5 5 0 0 0 2.7 2.7L7 6l2 2-1.3 1.3C4.5 9 1 5.5.7 2.3z" fill="#0b0b0b"/></svg></span>
          (570) 614-3098
        </li>
        <li class="contact__item">
          <span class="contact__icon"><svg width="9" height="9" viewBox="0 0 10 10"><rect x="1" y="2.5" width="8" height="5" fill="none" stroke="#0b0b0b" stroke-width="1.2"/><path d="M1 2.5l4 3 4-3" fill="none" stroke="#0b0b0b" stroke-width="1.2"/></svg></span>
          tomvarulek@quillbox.net
        </li>
        <li class="contact__item">
          <span class="contact__icon"><svg width="9" height="9" viewBox="0 0 10 10"><circle cx="5" cy="5" r="4" fill="none" stroke="#0b0b0b" stroke-width="1.1"/><path d="M1 5h8M5 1c-2 2.5-2 5.5 0 8M5 1c2 2.5 2 5.5 0 8" fill="none" stroke="#0b0b0b" stroke-width=".9"/></svg></span>
          www.tomvarulek.net
        </li>
      </ul>
    </div>
    <div class="divider"></div>
    <div class="brand brand--info">
      <span class="brand__dot"></span>
      <span class="brand__name">TOM VARULEK</span>
    </div>
    <div class="accent-tab accent-tab--right"></div>
  </section>

  <section class="card card--front" aria-label="Card front with name">
    <div class="brand brand--front">
      <span class="brand__dot"></span>
      <span class="brand__name">TOM VARULEK</span>
    </div>
  </section>
</main>
</body>
</html>
```